Indy Film Production Company/Studio

We need a business card designed from an existing logo. We are a digital studio/production company that caters to creating genre entertainment, like Action, Horror, and martial arts. The card along with the logo will be used to Brand the company from letter heads to banners. The design will also be used for postcards and Brochures. It should be professional and masculine.
Updates

Thank you to all the designers who have participated. I'm narrowing down who it will be. Thank you again.

Target Market(s)

Investors, Networks, Producers, and actors

Industry/Entity Type

Film Production

Contact Information for Business Card

Teodoro Valbuena
Producer/Writer/Director
www.kestrelpicturehouse.example

Requirements
Must have
• Website address, Facebook icon and Twitter icon possibly in the back of the card.
Nice to have
• Logline of Company: Follow The Action.

```html
<!DOCTYPE html>
<html lang="en">
<head>
<meta charset="utf-8">
<title>Kestrel Picture House — Business Card</title>
<link rel="stylesheet" href="https://fonts.googleapis.com/css2?family=Open+Sans:wght@400;700;800&display=swap">
<style>
  :root {
    --backdrop: #2a2c2f;
    --card-light: #ffffff;
    --card-dark: #050505;
    --ink-dark: #111111;
    --ink-light: #f4f4f4;
    --ink-muted: #bdbdbd;
  }
  * { margin: 0; padding: 0; box-sizing: border-box; }
  html, body {
    width: 1200px;
    height: 864px;
    overflow: hidden;
    background: var(--backdrop);
    font-family: "Open Sans", Arial, sans-serif;
  }
  .canvas {
    position: relative;
    width: 1200px;
    height: 864px;
  }
  .card {
    position: absolute;
    width: 620px;
    height: 354px;
    border-radius: 3px;
    box-shadow: 0 10px 30px rgba(0, 0, 0, 0.45);
  }
  .card--front {
    left: 230px;
    top: 50px;
    background: var(--card-light);
    display: flex;
    flex-direction: column;
    align-items: center;
    justify-content: center;
    gap: 14px;
  }
  .brand {
    display: flex;
    align-items: center;
    gap: 14px;
    color: var(--ink-dark);
  }
  .brand__square {
    width: 34px;
    height: 34px;
    background: var(--ink-dark);
  }
  .brand__name {
    font-weight: 800;
    font-size: 30px;
    letter-spacing: 1px;
    text-transform: uppercase;
  }
  .logline {
    color: var(--ink-dark);
    font-size: 14px;
    font-weight: 700;
    letter-spacing: 4px;
    text-transform: uppercase;
  }
  .card--back {
    left: 190px;
    top: 450px;
    background: var(--card-dark);
    color: var(--ink-light);
    text-align: center;
  }
  .contact__name {
    position: absolute;
    top: 46px;
    width: 100%;
    font-weight: 700;
    font-size: 16px;
    letter-spacing: 0.5px;
    text-transform: uppercase;
  }
  .contact__title {
    position: absolute;
    top: 70px;
    width: 100%;
    font-size: 13px;
  }
  .contact__lines {
    position: absolute;
    top: 128px;
    width: 100%;
    list-style: none;
    font-size: 13.5px;
    line-height: 17px;
  }
  .contact__address {
    position: absolute;
    top: 214px;
    width: 100%;
    font-size: 13.5px;
  }
  .social {
    position: absolute;
    top: 262px;
    width: 100%;
    display: flex;
    justify-content: center;
    gap: 14px;
    list-style: none;
  }
  .social__dot {
    width: 26px;
    height: 26px;
    border-radius: 50%;
    background: var(--ink-muted);
  }
</style>
</head>
<body>
  <main class="canvas">
    <section class="card card--front" aria-label="Card front">
      <div class="brand">
        <span class="brand__square" aria-hidden="true"></span>
        <span class="brand__name">Kestrel Picture House</span>
      </div>
      <p class="logline">Follow The Action</p>
    </section>

    <section class="card card--back" aria-label="Card back">
      <p class="contact__name">Teodoro Valbuena</p>
      <p class="contact__title">Producer/Writer/Director</p>
      <ul class="contact__lines">
        <li>044-555-0142</li>
        <li>123-555-0187</li>
        <li>hello@kestrelpicturehouse.example</li>
        <li>www.kestrelpicturehouse.example</li>
      </ul>
      <p class="contact__address">88 Harbor Lane | Millbrook, AB | 204519</p>
      <ul class="social" aria-label="Social profiles">
        <li class="social__dot" role="img" aria-label="Social network profile"></li>
        <li class="social__dot" role="img" aria-label="Social network profile"></li>
      </ul>
    </section>
  </main>
</body>
</html>
```